Letterhead, stationery and email signature for construction business

I need the letterhead, stationery and email signature designs for a construction business. I want them to have a corporate feel to them.

I've attached the logo for reference.

```html
<!DOCTYPE html>
<html lang="en">
<head>
<meta charset="utf-8">
<title>Norvane Projects — Stationery Suite</title>
<link href="https://fonts.googleapis.com/css2?family=Montserrat:wght@400;600;700&family=Open+Sans:wght@400;600&display=swap" rel="stylesheet">
<style>
  :root{
    --brand:#2f58a8;
    --brand-deep:#1f3f86;
    --ink:#44474f;
    --muted:#8a8d94;
    --paper:#ffffff;
    --bg-top:#ececec;
    --bg-bottom:#f4f4f4;
    --line:#d9dbe0;
  }
  *{box-sizing:border-box;margin:0;padding:0}
  html,body{width:1200px;height:1200px;overflow:hidden}
  body{position:relative;background:linear-gradient(var(--bg-top) 0 790px,var(--bg-bottom) 790px);font-family:"Open Sans",Arial,sans-serif;color:var(--ink)}
  .piece{position:absolute;background:var(--paper);box-shadow:0 2px 6px rgba(0,0,0,.12)}

  /* Wordmark: invented name stacked on two lines with a plain square */
  .brand{display:flex;align-items:center;gap:.3em;font-family:"Montserrat",Arial,sans-serif;font-weight:700;color:var(--ink);letter-spacing:.06em;white-space:nowrap;line-height:1}
  .brand::before{content:"";width:1.9em;height:1.9em;background:currentColor;flex:none}
  .brand__name{display:block}
  .brand--light{color:#fff}

  /* Letterhead */
  .letterhead{left:292px;top:98px;width:292px;height:416px;padding:22px 26px}
  .letterhead .brand{font-size:8px}
  .letterhead__contact{position:absolute;right:26px;top:20px;border-left:1px solid var(--line);padding-left:6px;font-size:4.6px;line-height:1.55;color:var(--muted);font-style:normal}
  .letterhead__body{margin-top:44px;font-size:4.6px;line-height:1.55;color:var(--muted)}
  .letterhead__body p{margin-bottom:7px}
  .letterhead__sign{display:block;margin-top:6px}
  .letterhead__foot{position:absolute;left:0;right:0;bottom:0;height:5px;background:var(--brand)}
  .letterhead__foot::before{content:"";position:absolute;left:0;top:0;width:20px;height:5px;background:var(--ink)}

  /* Folder cover */
  .cover{left:636px;top:82px;width:276px;height:434px;overflow:hidden}
  .cover__photo{position:absolute;inset:0;background:linear-gradient(160deg,#0d2f75 0%,#1a5fc9 45%,#3d8ee6 70%,#143c8c 100%)}
  .cover .brand{position:absolute;left:50%;top:28%;transform:translateX(-50%);font-size:20px}

  /* Business cards */
  .card{width:132px;height:75px}
  .card--front{left:186px;top:550px;background:var(--brand);display:flex;align-items:center;justify-content:center}
  .card--front .brand{font-size:9px}
  .card--back{left:186px;top:644px}
  .card--back .brand{font-size:6px;position:absolute;right:12px;top:9px}
  .card__name{position:absolute;left:9px;top:32px;font-size:4.6px;color:var(--brand);font-weight:600;line-height:1.4}
  .card__name span{display:block;color:var(--muted);font-weight:400}
  .card__lines{position:absolute;left:9px;bottom:7px;font-size:3.8px;line-height:1.45;color:var(--muted)}
  .card__addr{position:absolute;right:9px;bottom:11px;font-size:3.8px;line-height:1.45;color:var(--muted);text-align:right}
  .card__rule{position:absolute;left:0;right:0;bottom:0;height:3px;background:var(--brand)}

  /* Envelopes */
  .envelope{top:562px;width:294px;height:156px}
  .envelope--window{left:354px}
  .envelope--window .brand{position:absolute;left:20px;top:18px;font-size:8px}
  .envelope__addr{position:absolute;left:20px;bottom:18px;font-size:5px;line-height:1.5;color:var(--muted)}
  .envelope__window{position:absolute;right:22px;bottom:18px;width:58px;height:26px;border:1px solid var(--line);background:#f2f3f5}
  .envelope--flap{left:715px;background:#f7f7f7}
  .envelope__flap{position:absolute;left:0;right:0;top:0;height:46px;background:var(--brand);display:flex;align-items:center;justify-content:center}
  .envelope__flap .brand{font-size:10px}

  /* Email signature */
  .signature{left:712px;top:744px;width:230px;height:76px;padding:10px 12px}
  .signature__name{font-family:"Montserrat",Arial,sans-serif;font-weight:700;font-size:7.5px;color:var(--brand)}
  .signature__role{font-size:6px;color:var(--ink);margin-bottom:5px}
  .signature__list{list-style:none;font-size:5.8px;line-height:1.5;color:var(--ink)}
  .signature__list li{display:flex;align-items:center;gap:4px}
  .signature__list svg{width:6px;height:6px;fill:var(--brand-deep)}
  .signature .brand{position:absolute;right:12px;top:11px;font-size:8px}
  .signature__addr{position:absolute;right:12px;bottom:11px;font-size:5.8px;line-height:1.5;text-align:right}

  /* Presentation folder spread */
  .spread{left:58px;top:818px;width:488px;height:310px;display:flex}
  .spread__back{position:relative;width:244px;height:100%;background:linear-gradient(135deg,#3a64b5,var(--brand-deep))}
  .spread__back-info{position:absolute;left:0;right:0;bottom:40px;font-size:5.4px;line-height:1.6;color:#dfe6f5;text-align:center}
  .spread__front{position:relative;width:244px;height:100%}
  .spread__front .brand{position:absolute;left:50%;top:38%;transform:translateX(-50%);font-size:16px}
  .spread__url{position:absolute;right:28px;bottom:32px;font-size:5.6px;color:var(--ink)}

  /* Standing folder */
  .folder-closed{left:604px;top:850px;width:180px;height:280px}
  .folder-closed .brand{position:absolute;left:24px;top:108px;font-size:13px}
  .folder-closed__url{position:absolute;left:0;right:0;bottom:16px;text-align:center;font-size:4.6px}

  /* Open folder */
  .folder-open{left:834px;top:840px;width:280px;height:290px;display:flex}
  .folder-open__panel{position:relative;width:140px;height:100%;background:#f1f1f1}
  .folder-open__panel + .folder-open__panel{background:#f9f9f9}
  .folder-open__pocket{position:absolute;left:0;right:0;bottom:0;height:82px;background:var(--brand)}
  .folder-open__panel > .brand{position:absolute;right:12px;top:14px;font-size:6px}
  .folder-open__card{position:absolute;left:74px;bottom:22px;width:48px;height:30px;background:#fff;box-shadow:0 1px 2px rgba(0,0,0,.2)}
  .folder-open__card .brand{position:absolute;right:4px;top:4px;font-size:3.4px}
</style>
</head>
<body>

<section class="piece letterhead">
  <div class="brand"><span class="brand__name">NORVANE<br>PROJECTS</span></div>
  <address class="letterhead__contact">4820 Meridian Park Drive,<br>Lakeside, CA 90417<br>(555) 310-0142<br>info@norvane.com<br>www.norvane.com</address>
  <div class="letterhead__body">
    <p>Dear customer,</p>
    <p>Lorem ipsum dolor sit amet, consectetur adipiscing elit, sed do eiusmod tempor incididunt ut labore et dolore magna aliqua. Ut enim ad minim veniam, quis nostrud exercitation ullamco laboris nisi ut aliquip ex ea commodo consequat. Duis aute irure dolor in reprehenderit in voluptate velit esse cillum dolore eu fugiat nulla pariatur. Excepteur sint occaecat cupidatat non proident, sunt in culpa qui officia deserunt mollit anim id est laborum.</p>
    <p>Lorem ipsum dolor sit amet, consectetur adipiscing elit, sed do eiusmod tempor incididunt ut labore et dolore magna aliqua. Ut enim ad minim veniam, quis nostrud exercitation ullamco laboris nisi ut aliquip ex ea commodo consequat. Duis aute irure dolor in reprehenderit in voluptate velit esse cillum dolore eu fugiat nulla pariatur. Excepteur sint occaecat cupidatat non proident, sunt in culpa qui officia deserunt mollit anim id est laborum.</p>
    <p>Lorem ipsum dolor sit amet, consectetur adipiscing elit, sed do eiusmod tempor incididunt ut labore et dolore magna aliqua. Ut enim ad minim veniam, quis nostrud exercitation ullamco laboris nisi ut aliquip ex ea commodo consequat. Duis aute irure dolor in reprehenderit in voluptate velit esse cillum dolore eu fugiat nulla pariatur. Excepteur sint occaecat cupidatat non proident, sunt in culpa qui officia deserunt mollit anim id est laborum.</p>
    <p>Lorem ipsum dolor sit amet, consectetur adipiscing elit, sed do eiusmod tempor incididunt ut labore et dolore magna aliqua. Ut enim ad minim veniam, quis nostrud exercitation ullamco laboris nisi ut aliquip ex ea commodo consequat. Duis aute irure dolor in reprehenderit.</p>
    <p>Yours Sincerely,</p>
    <svg class="letterhead__sign" width="22" height="16" viewBox="0 0 22 16"><path d="M3 12c2-8 4-9 5-4s-2 7 1 2 4-6 5 0 3-3 5-5" fill="none" stroke="#333" stroke-width=".8"/></svg>
  </div>
  <div class="letterhead__foot"></div>
</section>

<section class="piece cover">
  <div class="cover__photo" role="img" aria-label="Upward view of glass office towers and a construction crane against a blue sky"></div>
  <div class="brand brand--light"><span class="brand__name">NORVANE<br>PROJECTS</span></div>
</section>

<section class="piece card card--front">
  <div class="brand brand--light"><span class="brand__name">NORVANE<br>PROJECTS</span></div>
</section>

<section class="piece card card--back">
  <div class="brand"><span class="brand__name">NORVANE<br>PROJECTS</span></div>
  <p class="card__name">MARCUS T. ELLERY<span>Founder &amp; CEO</span></p>
  <p class="card__lines">(555) 310-0142<br>info@norvane.com<br>www.norvane.com</p>
  <p class="card__addr">Norvane Projects, Ltd.<br>4820 Meridian Park Drive<br>Lakeside, CA 90417</p>
  <div class="card__rule"></div>
</section>

<section class="piece envelope envelope--window">
  <div class="brand"><span class="brand__name">NORVANE<br>PROJECTS</span></div>
  <p class="envelope__addr">Norvane Projects, Ltd.<br>4820 Meridian Park Drive<br>Lakeside, CA 90417</p>
  <div class="envelope__window"></div>
</section>

<section class="piece envelope envelope--flap">
  <div class="envelope__flap"><div class="brand brand--light"><span class="brand__name">NORVANE<br>PROJECTS</span></div></div>
</section>

<section class="piece signature">
  <p class="signature__name">MARCUS T. ELLERY</p>
  <p class="signature__role">Founder &amp; CEO</p>
  <ul class="signature__list">
    <li><svg viewBox="0 0 10 10"><path d="M2 1l2 .3.6 2-1 1a6 6 0 0 0 2.2 2.2l1-1 2 .6L9 8c-.2.8-1 1-1.6 1A7.5 7.5 0 0 1 1 2.6C1 2 1.2 1.2 2 1z"/></svg>(555) 310-0142</li>
    <li><svg viewBox="0 0 10 10"><path d="M1 2h8v6H1z"/></svg>info@norvane.com</li>
    <li><svg viewBox="0 0 10 10"><circle cx="5" cy="5" r="4"/></svg>www.norvane.com</li>
  </ul>
  <div class="brand"><span class="brand__name">NORVANE<br>PROJECTS</span></div>
  <p class="signature__addr">4820 Meridian Park Drive,<br>Lakeside, CA 90417</p>
</section>

<section class="piece spread">
  <div class="spread__back">
    <p class="spread__back-info">Norvane Projects, Ltd.<br>4820 Meridian Park Drive, Lakeside, CA 90417<br>(555) 310-0142 · info@norvane.com<br>www.norvane.com</p>
  </div>
  <div class="spread__front">
    <div class="brand"><span class="brand__name">NORVANE<br>PROJECTS</span></div>
    <p class="spread__url">www.norvane.com</p>
  </div>
</section>

<section class="piece folder-closed">
  <div class="brand"><span class="brand__name">NORVANE<br>PROJECTS</span></div>
  <p class="folder-closed__url">www.norvane.com</p>
</section>

<section class="piece folder-open">
  <div class="folder-open__panel"><div class="folder-open__pocket"></div></div>
  <div class="folder-open__panel">
    <div class="brand"><span class="brand__name">NORVANE<br>PROJECTS</span></div>
    <div class="folder-open__pocket"></div>
    <div class="folder-open__card"><div class="brand"><span class="brand__name">NORVANE<br>PROJECTS</span></div></div>
  </div>
</section>

</body>
</html>
```